Food Platform with Economic-Social Cause, needs folder design, corporate and stationery

Technology company linked to food with strong social commitment, needs to dazzle customers and shareholders, with elegant, minimalist and distinguished design of folder, corporate card and other stationery. The Company proposes networking by creating a community committed to the economic and social aspects. The humanization of the economy. We attach a model of another company card and logo to use in proposals.
Updates
UNFORTUNATELY WE CANNOT FIND A DESIGN THAT DOES NOT REPRESENT WHAT WE ARE LOOKING FOR
Target Market(s)
Companies, entrepreneurs, food producers and the general public
Industry/Entity Type
Food companies, Foundations fight against hunger, Citizenship.
Colors
Designer to choose colors to be used in the design.
Requirements
Must have
- elegance, minimalism, graphic communication of networking for a humanized economy. phrase "activating consciousness" "united for a cause"
Nice to have
- human network graph. Chain of favors. Preferred shades: white, gold or champagne and combination.human network graph. Chain of favors. Preferred shades: white, gold or champagne and combination.
Should not have
- dark communication

```html
<!DOCTYPE html>
<html lang="en">
<head>
<meta charset="utf-8">
<title>Alma Group — Folder and Stationery</title>
<link href="https://fonts.googleapis.com/css2?family=Open+Sans:wght@400;600&display=swap" rel="stylesheet">
<style>
  :root {
    --backdrop: #e7e8ea;
    --paper: #ffffff;
    --champagne: #d2b29e;
    --champagne-soft: #e6d3c6;
    --ghost: #f0f0f1;
    --ink: #3a3a3a;
    --ink-soft: #6b6b6b;
    --window: #d3d4d6;
  }
  * { box-sizing: border-box; margin: 0; padding: 0; }
  html, body { width: 1200px; height: 938px; overflow: hidden; }
  body {
    position: relative;
    background: var(--backdrop);
    font-family: "Open Sans", Arial, sans-serif;
    color: var(--ink);
  }
  .sheet { position: absolute; background: var(--paper); overflow: hidden; }

  .brand { position: absolute; display: flex; align-items: center; gap: 4px; color: var(--champagne); font-weight: 400; white-space: nowrap; }
  .brand__dot { border: 1px solid var(--champagne); border-radius: 50%; flex: none; }
  .brand--light { color: var(--paper); }
  .brand--light .brand__dot { border-color: var(--paper); }

  .deco-ring { position: absolute; border-radius: 50%; pointer-events: none; }

  .letter__title { position: absolute; font-size: 5px; color: var(--ink); }
  .letter__body { position: absolute; font-size: 3.4px; line-height: 6.3px; color: var(--ink-soft); text-align: justify; }
  .letter__body p + p { margin-top: 6.3px; }
  .letter__signer { position: absolute; font-size: 3.6px; color: var(--ink); }
  .letter__role { position: absolute; font-size: 1.8px; color: var(--ink-soft); }
  .letter__signature { position: absolute; background: var(--ink-soft); opacity: .35; border-radius: 2px; }

  .contact-row { position: absolute; display: flex; align-items: center; gap: 3px; font-size: 3.3px; color: var(--champagne); white-space: nowrap; }
  .contact-row--grey { color: #9a9a9a; }
  .contact-icon { width: 4px; height: 4px; border-radius: 1px; background: currentColor; flex: none; opacity: .8; }

  .pocket-url { position: absolute; font-size: 4.6px; color: var(--paper); }
</style>
</head>
<body>

<!-- Presentation folder, open -->
<section class="folder">
  <div class="sheet folder__inside-left" style="left:165px;top:62px;width:276px;height:389px;"></div>
  <div class="sheet folder__inside-right" style="left:441px;top:64px;width:276px;height:387px;"></div>

  <!-- Letterhead tucked in the pocket -->
  <article class="sheet letter" style="left:449px;top:69px;width:261px;height:380px;box-shadow:0 0 2px rgba(0,0,0,.12);">
    <div class="deco-ring" style="left:170px;top:112px;width:200px;height:200px;border:7px solid var(--ghost);"></div>
    <div class="brand" style="left:44px;top:88px;font-size:12px;">
      <span class="brand__dot" style="width:18px;height:18px;"></span>Alma Group
    </div>
    <h2 class="letter__title" style="left:44px;top:130px;font-weight:400;">Lorem ipsum</h2>
    <div class="letter__body" style="left:44px;top:147px;width:187px;">
      <p>Lorem ipsum dolor sit amet, consectetuer adipiscing elit, sed diam nonummy nibh euismod tincidunt ut laoreet dolore magna aliquam erat volutpat. Ut wisi enim ad minim veniam, quis nostrud exerci tation ullamcorper suscipit lobortis nisl ut aliquip ex ea commodo consequat. Duis autem vel eum iriure dolor in hendrerit in vulputate velit esse molestie consequat, vel illum dolore eu feugiat nulla facilisis at vero eros et accumsan et iusto odio dignissim qui blandit praesent luptatum zzril delenit augue duis dolore te feugait nulla facilisi. Lorem ipsum dolor sit amet, cons ectetuer adipiscing elit, sed diam nonummy nibh euismod tincidunt ut laoreet dolore magna aliquam erat volutpat. Ut wisi enim ad minim veniam, quis nostrud exerci tation ullamcorper suscipit lobortis nisl ut aliquip ex ea commodo consequat.</p>
      <p>Lorem ipsum dolor sit amet, consectetuer adipiscing elit, sed diam nonummy nibh euismod tincidunt ut laoreet dolore magna aliquam erat volutpat. Ut wisi enim ad minim veniam, quis nostrud exerci tation ullamcorper suscipit lobortis nisl ut aliquip ex ea commodo consequat. Duis autem vel eum iriure dolor in hendrerit in vulputate velit esse molestie consequat, vel illum dolore eu feugiat nulla facilisis at vero eros et accumsan et iusto odio dignissim qui blandit praesent luptatum zzril delenit augue duis dolore te feugait nulla facilisi. Lorem ipsum dolor sit amet, cons ectetuer adipiscing elit, sed diam nonummy nibh euismod tincidunt ut laoreet dolore magna aliquam erat volutpat. Ut wisi enim ad minim veniam, quis nostrud exerci tation ullamcorper suscipit lobortis nisl ut aliquip ex ea commodo consequat.</p>
    </div>
    <div class="letter__signer" style="left:44px;top:265px;">Alma</div>
    <div class="letter__role" style="left:44px;top:273px;">Co-Founder &amp; CEO</div>
    <div class="letter__signature" role="img" aria-label="Handwritten signature" style="left:44px;top:282px;width:14px;height:8px;"></div>
  </article>

  <!-- Folder pocket -->
  <svg class="folder__pocket" style="position:absolute;left:441px;top:342px;" width="276" height="109" viewBox="0 0 276 109" aria-hidden="true">
    <path d="M0 109 L72 10 Q79 1 90 1 L276 1 L276 109 Z" fill="var(--champagne)"/>
  </svg>
  <div class="pocket-url" style="left:591px;top:430px;">www.yourwebsite.com</div>
  <div class="brand brand--light" style="left:659px;top:422px;font-size:8px;">
    <span class="brand__dot" style="width:12px;height:12px;"></span>Alma Group
  </div>
</section>

<!-- Folder cover -->
<section class="sheet cover" style="left:165px;top:473px;width:276px;height:386px;">
  <div class="deco-ring" style="left:138px;top:60px;width:276px;height:276px;border:9px solid var(--champagne);"></div>
  <div class="brand" style="left:31px;top:183px;font-size:15px;">
    <span class="brand__dot" style="width:25px;height:25px;"></span>Alma Group
  </div>
</section>

<!-- Letterhead -->
<article class="sheet letter" style="left:458px;top:480px;width:262px;height:370px;">
  <div class="deco-ring" style="left:158px;top:108px;width:196px;height:196px;border:7px solid var(--ghost);"></div>
  <div class="brand" style="left:48px;top:84px;font-size:12px;">
    <span class="brand__dot" style="width:18px;height:18px;"></span>Alma Group
  </div>
  <h2 class="letter__title" style="left:48px;top:127px;font-weight:400;">Lorem ipsum</h2>
  <div class="letter__body" style="left:48px;top:144px;width:187px;">
    <p>Lorem ipsum dolor sit amet, consectetuer adipiscing elit, sed diam nonummy nibh euismod tincidunt ut laoreet dolore magna aliquam erat volutpat. Ut wisi enim ad minim veniam, quis nostrud exerci tation ullamcorper suscipit lobortis nisl ut aliquip ex ea commodo consequat. Duis autem vel eum iriure dolor in hendrerit in vulputate velit esse molestie consequat, vel illum dolore eu feugiat nulla facilisis at vero eros et accumsan et iusto odio dignissim qui blandit praesent luptatum zzril delenit augue duis dolore te feugait nulla facilisi. Lorem ipsum dolor sit amet, cons ectetuer adipiscing elit, sed diam nonummy nibh euismod tincidunt ut laoreet dolore magna aliquam erat volutpat. Ut wisi enim ad minim veniam, quis nostrud exerci tation ullamcorper suscipit lobortis nisl ut aliquip ex ea commodo consequat.</p>
    <p>Lorem ipsum dolor sit amet, consectetuer adipiscing elit, sed diam nonummy nibh euismod tincidunt ut laoreet dolore magna aliquam erat volutpat. Ut wisi enim ad minim veniam, quis nostrud exerci tation ullamcorper suscipit lobortis nisl ut aliquip ex ea commodo consequat. Duis autem vel eum iriure dolor in hendrerit in vulputate velit esse molestie consequat, vel illum dolore eu feugiat nulla facilisis at vero eros et accumsan et iusto odio dignissim qui blandit praesent luptatum zzril delenit augue duis dolore te feugait nulla facilisi. Lorem ipsum dolor sit amet, cons ectetuer adipiscing elit, sed diam nonummy nibh euismod tincidunt ut laoreet dolore magna aliquam erat volutpat. Ut wisi enim ad minim veniam, quis nostrud exerci tation ullamcorper suscipit lobortis nisl ut aliquip ex ea commodo consequat.</p>
  </div>
  <div class="letter__signer" style="left:48px;top:262px;">Alma</div>
  <div class="letter__role" style="left:48px;top:270px;">Co-Founder &amp; CEO</div>
  <div class="letter__signature" role="img" aria-label="Handwritten signature" style="left:48px;top:279px;width:14px;height:8px;"></div>
  <footer>
    <div class="contact-row contact-row--grey" style="left:52px;top:347px;"><span class="contact-icon"></span>(123) 123-4567</div>
    <div class="contact-row contact-row--grey" style="left:98px;top:347px;"><span class="contact-icon"></span>youremail@gmail.com</div>
    <div class="contact-row contact-row--grey" style="left:155px;top:347px;"><span class="contact-icon"></span>yourwebsite.com</div>
    <div class="contact-row contact-row--grey" style="left:206px;top:347px;"><span class="contact-icon"></span>your address 1234</div>
  </footer>
</article>

<!-- Business card, front -->
<section class="sheet card card--front" style="left:747px;top:480px;width:110px;height:63px;">
  <div class="brand" style="left:33px;top:25px;font-size:8px;">
    <span class="brand__dot" style="width:12px;height:12px;"></span>Alma Group
  </div>
</section>

<!-- Business card, back -->
<section class="sheet card card--back" style="left:886px;top:480px;width:111px;height:63px;">
  <div class="deco-ring" style="left:80px;top:1px;width:62px;height:62px;background:var(--champagne);"></div>
  <div style="position:absolute;left:9px;top:15px;font-size:5.5px;color:var(--champagne);">Your Name</div>
  <div style="position:absolute;left:27px;top:22px;font-size:1.8px;color:var(--champagne);">Director</div>
  <div class="contact-row" style="left:9px;top:30px;font-size:3px;"><span class="contact-icon"></span>(123) 123-4567</div>
  <div class="contact-row" style="left:9px;top:36.5px;font-size:3px;"><span class="contact-icon"></span>youremail@gmail.com</div>
  <div class="contact-row" style="left:9px;top:43px;font-size:3px;"><span class="contact-icon"></span>yourwebsite.com</div>
  <div class="contact-row" style="left:9px;top:49.5px;font-size:3px;"><span class="contact-icon"></span>your address, NC 1234</div>
</section>

<!-- Envelope, back with flap -->
<section class="sheet envelope envelope--back" style="left:746px;top:569px;width:301px;height:131px;">
  <svg style="position:absolute;left:0;top:0;" width="301" height="42" viewBox="0 0 301 42" aria-hidden="true">
    <path d="M2 0 L8 32 Q10 40 20 40 L281 40 Q291 40 293 32 L299 0" fill="none" stroke="#e2e2e4" stroke-width="1"/>
  </svg>
  <span class="brand__dot" style="position:absolute;left:139px;top:10px;width:22px;height:22px;border:1px solid var(--champagne);border-radius:50%;"></span>
  <div class="deco-ring" style="left:262px;top:47px;width:82px;height:82px;border:3px solid var(--ghost);"></div>
  <div class="brand" style="left:17px;top:100px;font-size:8px;">
    <span class="brand__dot" style="width:13px;height:13px;"></span>Alma Group
  </div>
</section>

<!-- Envelope, front with address window -->
<section class="sheet envelope envelope--front" style="left:746px;top:717px;width:301px;height:131px;">
  <div class="brand" style="left:20px;top:70px;font-size:6px;">
    <span class="brand__dot" style="width:9px;height:9px;"></span>Alma Group
  </div>
  <div class="contact-row" style="left:19px;top:89px;font-size:3px;"><span class="contact-icon"></span>(123) 123-4567</div>
  <div class="contact-row" style="left:19px;top:95.5px;font-size:3px;"><span class="contact-icon"></span>youremail@gmail.com</div>
  <div class="contact-row" style="left:19px;top:102px;font-size:3px;"><span class="contact-icon"></span>yourwebsite.com</div>
  <div class="contact-row" style="left:19px;top:108.5px;font-size:3px;"><span class="contact-icon"></span>your address, NC 1234</div>
  <div class="envelope__window" style="position:absolute;left:181px;top:75px;width:101px;height:31px;background:var(--window);border-radius:4px;"></div>
</section>

</body>
</html>
```